Business Card Design

We like to use greens as you will see in our logo (but not TOO much green). We are a Dental Clinic in a somewhat eccentric community. We do not like the dated sharp designs which we see many dentists use. We're looking for something bright and fresh while still maintaining the integrity of the profession. Elegance is not necessarily what we are going for... we need for the design to be "mature" but also up-lifting.

See our logo.
Updates

Project Deadline Extended
Reason: We have 5 designs which we like. But we'd like to see a few more before committing to a design.

Project Deadline Extended
Reason: We are awaiting revisions to this project. We are still welcoming designs while we wait to see if designers are able to provide to us the revisions we require in order to proceed with a selection.

Target Market(s)

Younger families - ages late 20's to early 40's

Industry/Entity Type

Business

Contact Information for Business Card

Corwel T. Banfry DDS 2730 W. Halvert Rd. Ste. 7 Larkfield 48391 (248)555-0174 FX (248)555-0189 info@BrightwellDentalCareMi.com BrigthwellDentalCareMi.com on the back of the card we need an appointment reminder (For____ Date___ Time____) with "If you are unable to keep your appointment, kindly give 48 hours notice" at the bottom. No use of teeth in the design. DOUBLE SIDED DESIGN

Requirements
Should not have
• The use of pictures of teeth

```html
<!DOCTYPE html>
<html lang="en">
<head>
<meta charset="utf-8">
<title>Brightwell Dental Care – Business Card</title>
<link href="https://fonts.googleapis.com/css2?family=PT+Sans:ital,wght@0,400;0,700;1,400&family=Marcellus&display=swap" rel="stylesheet">
<style>
  :root {
    --green-deep: #1f6b35;
    --green-mid: #3c8a3f;
    --green-light: #8cc63f;
    --ink: #333333;
    --paper: #ffffff;
    --backdrop: #ecece8;
    --dots: #777777;
    --box-line: #555555;
  }
  * { margin: 0; padding: 0; box-sizing: border-box; }
  html, body { width: 1200px; height: 1178px; overflow: hidden; }
  body {
    background: var(--backdrop);
    font-family: "PT Sans", "Helvetica Neue", Arial, sans-serif;
    color: var(--ink);
    position: relative;
  }
  .card {
    position: absolute;
    width: 917px;
    height: 525px;
    background: var(--paper);
    box-shadow: 0 3px 10px rgba(0,0,0,.18);
    overflow: hidden;
  }

  /* ---------- front ---------- */
  .card-front { left: 251px; top: 24px; }
  .brand {
    position: absolute;
    display: flex;
    align-items: center;
    gap: 16px;
    color: var(--green-deep);
    font-weight: 700;
  }
  .brand-dot {
    border-radius: 50%;
    background: var(--green-light);
    flex: none;
  }
  .brand-name { line-height: 1; }
  .brand-name span { display: block; }
  .card-front .brand { left: 70px; top: 165px; }
  .card-front .brand-dot { width: 54px; height: 54px; }
  .card-front .brand-name .line-1 { font-size: 58px; }
  .card-front .brand-name .line-2 { font-size: 34px; margin-top: 6px; letter-spacing: 1px; }

  .divider {
    position: absolute;
    left: 488px; top: 96px;
    width: 2px; height: 269px;
    background: #9a9a9a;
  }
  .contact { position: absolute; left: 509px; top: 100px; }
  .contact-name {
    font-size: 33px; font-weight: 700; color: var(--green-deep); line-height: 1.1;
  }
  .contact-title { font-size: 23px; margin-top: 4px; }
  .contact-list { list-style: none; margin-top: 30px; }
  .contact-list li {
    display: flex; align-items: center; gap: 8px;
    font-size: 22px; height: 40px;
  }
  .contact-list svg { width: 20px; height: 20px; flex: none; }

  .front-rule {
    position: absolute; left: 0; right: 0; top: 454px;
    height: 4px; background: var(--green-mid);
  }
  .address-band {
    position: absolute; left: 0; right: 0; bottom: 0;
    height: 56px; background: var(--green-deep);
    color: #fff; font-size: 22px;
    display: flex; align-items: center; justify-content: center;
  }

  /* ---------- back ---------- */
  .card-back { left: 22px; top: 608px; }
  .card-back .brand { left: 74px; top: 40px; gap: 12px; }
  .card-back .brand-dot { width: 32px; height: 32px; }
  .card-back .brand-name .line-1 { font-size: 40px; }
  .card-back .brand-name .line-2 { font-size: 24px; margin-top: 4px; letter-spacing: 1px; }

  .appt-title {
    position: absolute; left: 79px; top: 170px;
    font-family: "Marcellus", "Times New Roman", serif;
    font-size: 34px; color: var(--green-deep); letter-spacing: 1px;
  }
  .field {
    position: absolute; left: 82px;
    display: flex; align-items: baseline;
    font-size: 25px;
  }
  .dots {
    border-bottom: 2px dotted var(--dots);
    height: 1px; margin: 0 6px;
    align-self: flex-end; margin-bottom: 8px;
  }
  .field-name { top: 240px; }
  .field-name .dots { width: 505px; margin-left: 16px; }
  .field-date { top: 305px; }
  .field-date .dots.date { width: 165px; margin-left: 22px; margin-right: 10px; }
  .field-date .dots.time { width: 155px; margin-left: 10px; margin-right: 2px; }
  .field-next { top: 370px; }
  .slot {
    position: absolute; top: 373px;
    width: 164px; height: 35px;
    border: 2px solid var(--box-line); border-radius: 4px;
  }
  .slot-1 { left: 326px; }
  .slot-2 { left: 530px; }

  .days { position: absolute; left: 740px; top: 75px; list-style: none; }
  .days li {
    position: absolute; left: 0;
    width: 151px; height: 34px;
    display: flex; align-items: center; justify-content: space-between;
    font-size: 25px; font-weight: 700;
  }
  .days li::after {
    content: ""; width: 57px; height: 32px;
    border: 2px solid var(--box-line); border-radius: 3px;
  }
  .days li:nth-child(1) { top: 0; }
  .days li:nth-child(2) { top: 64px; }
  .days li:nth-child(3) { top: 126px; }
  .days li:nth-child(4) { top: 190px; }
  .days li:nth-child(5) { top: 248px; }
  .days li:nth-child(6) { top: 304px; }

  .notice {
    position: absolute; left: 0; right: 0; top: 450px;
    text-align: center; font-style: italic; font-size: 25px;
  }
  .back-band {
    position: absolute; left: 0; right: 0; bottom: 4px;
    height: 13px; background: var(--green-deep);
  }
</style>
</head>
<body>

<section class="card card-front" aria-label="Business card front">
  <div class="brand">
    <span class="brand-dot"></span>
    <div class="brand-name"><span class="line-1">Brightwell</span><span class="line-2">DENTAL CARE</span></div>
  </div>

  <div class="divider"></div>

  <div class="contact">
    <p class="contact-name">Corwel T. Banfry</p>
    <p class="contact-title">DDS</p>
    <ul class="contact-list">
      <li>
        <svg viewBox="0 0 20 20" aria-hidden="true"><circle cx="10" cy="10" r="9" fill="none" stroke="#333" stroke-width="1.5"/><path d="M6.5 5.5l2 0 1 3-1.3 1a6 6 0 0 0 2.8 2.8l1-1.3 3 1v2a1.5 1.5 0 0 1-1.5 1.2A8 8 0 0 1 5 7a1.5 1.5 0 0 1 1.5-1.5z" fill="#333"/></svg>
        (555)555-0174
      </li>
      <li>
        <svg viewBox="0 0 20 20" aria-hidden="true"><rect x="5" y="3" width="10" height="6" fill="none" stroke="#333" stroke-width="1.5"/><rect x="2" y="8" width="16" height="7" rx="1.5" fill="#333"/><rect x="5" y="13" width="10" height="4" fill="#fff" stroke="#333" stroke-width="1.2"/></svg>
        (555)555-0189
      </li>
      <li>
        <svg viewBox="0 0 20 20" aria-hidden="true"><rect x="2" y="5" width="16" height="11" rx="1" fill="#333"/><path d="M2.5 5.5L10 11l7.5-5.5" fill="none" stroke="#fff" stroke-width="1.4"/></svg>
        info@BrightwellDentalCareMi.com
      </li>
      <li>
        <svg viewBox="0 0 20 20" aria-hidden="true"><g fill="none" stroke="#333" stroke-width="1.4"><circle cx="10" cy="10" r="8"/><ellipse cx="10" cy="10" rx="3.5" ry="8"/><path d="M2 10h16M3.5 6h13M3.5 14h13"/></g></svg>
        BrigthwellDentalCareMi.com
      </li>
    </ul>
  </div>

  <div class="front-rule"></div>
  <div class="address-band">2730 W. Halvert Rd. Ste. 7 Larkfield 48391</div>
</section>

<section class="card card-back" aria-label="Appointment card back">
  <div class="brand">
    <span class="brand-dot"></span>
    <div class="brand-name"><span class="line-1">Brightwell</span><span class="line-2">DENTAL CARE</span></div>
  </div>

  <h2 class="appt-title">YOUR APPOINTMENT</h2>

  <div class="field field-name">Name :<span class="dots"></span></div>
  <div class="field field-date">Date :<span class="dots date"></span>Time :<span class="dots time"></span>am / pm</div>
  <div class="field field-next">Next Appointment</div>
  <div class="slot slot-1"></div>
  <div class="slot slot-2"></div>

  <ul class="days">
    <li>MON</li>
    <li>TUE</li>
    <li>WED</li>
    <li>THU</li>
    <li>FRI</li>
    <li>SAT</li>
  </ul>

  <p class="notice">If you are unable to keep your appointment, kindly give 48 hours notice</p>
  <div class="back-band"></div>
</section>

</body>
</html>
```